Website Update for Global Company - Solar Technology - LeafCore

We recently released our first version of our website velirox.com. However despite a longer process of developing the page, it is still missing the elements of a brilliant website. (Currently it looks dead and boring) We are having problems integrating our logo and want to create a more catching site. The task involves an updated and without changing most of main elements in the existing page. (Unless you can do it even better) The blue color needs to be kept but can be changed within the blue-spectrum. The logo text (VELIROX) must be better integrated in the site, however the main logo could be used in elements like we have tried with the background. The surface of the logo could be changed to 3D or metallic, or any other theme that would make the site more complete.
It would be good if some elements of the site could be used on business cards and invoices to keep the company identity.
Velirox is a new development company specialized in green energy and sustainable development. We do design, engineering, manufacturing, sourcing and other processes related to product development – both as consultants and for own products.
Keep the look of the site as professional as possible, and with a cooperate-looking style.

Link to existing page: www.velirox.com

Brief Update : After reviewing the designs we would like all new and current designers to make more bold designs that stands out from the rest. We do not like the standard layout that looks like any other cooperate homepage. We want a very unique and very lively page - with faded images and effects when hoovering like seen on our existing page. Try make all elements blend together, and use faded background images instead of just white color - or something else.

Make the site unique !

Industry/Entity Type

Solar Energy

Contact Information for Business Card

Owner/Founder/CEO : Jonas Ulfkær Lindholm
Company name: Velirox ApS
Email: jonas.ulfkaer@velirox.dk
Phone: +45 71 82 64 93
Slogan Sustainable Development
Address: Kildevej 58, 2
DK-8630 Halvby, Denmark

Number of Pages Required

3 page

Font styles to use
Serif
Sans Serif

Colors
0555a3
85acd3
cedeed
3176b5
cee9f5
85cae6
0293ce
86cfc6
33b8a4

```html
<!DOCTYPE html>
<html lang="en">
<head>
<meta charset="utf-8">
<title>Velirox – Sustainable Solutions</title>
<link href="https://fonts.googleapis.com/css2?family=Open+Sans:wght@400;600;700&family=Roboto:wght@300;400;500;700&display=swap" rel="stylesheet">
<style>
:root{
  --blue-deep:#0555a3;
  --blue-mid:#3176b5;
  --blue-sky:#0293ce;
  --blue-soft:#85acd3;
  --blue-pale:#cedeed;
  --blue-ice:#cee9f5;
  --teal:#33b8a4;
  --navy:#0b3566;
  --navy-dark:#072648;
  --ink:#2e3a46;
  --grey:#6f7a85;
  --white:#ffffff;
  --green:#7dbb3c;
}
*{box-sizing:border-box;margin:0;padding:0}
html,body{width:1200px;height:2280px;overflow:hidden}
body{position:relative;font-family:"Open Sans",Arial,sans-serif;color:var(--ink);background:var(--white)}
section,header,footer{position:absolute;left:0;width:1200px}

/* header */
.site-header{top:0;height:100px;background:linear-gradient(#ffffff,#eef2f6);border-bottom:1px solid #d6dde4}
.brand{position:absolute;left:70px;top:28px;display:flex;align-items:center;gap:10px}
.brand-dot{width:18px;height:18px;border-radius:50%;background:var(--blue-mid)}
.brand-name{font-family:"Open Sans",sans-serif;font-weight:700;font-size:32px;color:var(--ink);line-height:1}
.header-phone{position:absolute;right:90px;top:14px;display:flex;align-items:center;gap:8px;font-size:15px;font-weight:600;color:var(--blue-deep)}
.main-nav{position:absolute;right:86px;top:52px;display:flex;gap:6px}
.main-nav a{font-family:"Roboto",sans-serif;font-size:13px;font-weight:500;color:var(--ink);text-decoration:none;padding:6px 10px}
.main-nav a.active{border:1px solid var(--blue-mid);color:var(--blue-mid)}

/* hero */
.hero{top:100px;height:480px;background:linear-gradient(110deg,#0c3f72 0%,#1668a8 45%,#0f5c9a 70%,#0a3f74 100%)}
.hero-visual{position:absolute;left:0;top:0;width:640px;height:480px;background:radial-gradient(ellipse at 45% 55%,rgba(133,202,230,.45),rgba(5,85,163,0) 70%)}
.hero-title{position:absolute;left:700px;top:165px;width:420px;text-align:right;font-family:"Roboto",sans-serif;font-weight:500;font-size:29px;line-height:1.35;color:var(--white)}
.slider-dots{position:absolute;display:flex;gap:8px}
.slider-dots span{width:12px;height:12px;border-radius:50%;border:2px solid var(--white)}
.slider-dots span.on{background:var(--white)}
.hero .slider-dots{right:110px;top:445px}

/* services */
.services{top:580px;height:400px;background:linear-gradient(#ffffff,#f4f7fa)}
.section-title{text-align:center;font-family:"Roboto",sans-serif;font-weight:500;font-size:30px;color:var(--ink)}
.section-title strong{color:var(--blue-deep);font-weight:700}
.services .section-title{margin-top:40px}
.title-rule{width:70px;height:3px;background:var(--blue-sky);margin:10px auto 0}
.service-list{position:absolute;left:140px;top:125px;width:920px;display:flex;justify-content:space-between}
.service{width:150px;text-align:center}
.service-icon{width:70px;height:70px;border-radius:50%;background:var(--blue-deep);margin:0 auto;display:flex;align-items:center;justify-content:center;box-shadow:0 0 0 4px var(--blue-pale)}
.service h3{font-size:15px;font-weight:600;margin:16px 0 8px;color:var(--ink)}
.service p{font-size:11px;line-height:1.5;color:var(--grey)}
.more-btn{display:inline-block;margin-top:12px;border:1px solid #c4ccd4;font-size:10px;color:var(--grey);padding:3px 10px;background:var(--white)}
.arrow{position:absolute;top:195px;font-size:34px;color:#48525c;font-family:"Roboto",sans-serif}
.arrow.left{left:78px}.arrow.right{right:78px}

/* welcome */
.welcome{top:980px;height:480px;background:linear-gradient(180deg,#e1f1f9,var(--blue-ice) 55%,#bfe0f0)}
.welcome .section-title{margin-top:45px;color:var(--blue-mid);font-size:28px}
.welcome-intro{width:980px;margin:16px auto 0;text-align:center;font-size:12px;line-height:1.7;color:#4e6274}
.info-card{position:absolute;top:210px;width:320px;height:230px;background:var(--white);text-align:center;padding-top:58px;box-shadow:0 2px 8px rgba(5,85,163,.12)}
.info-card.who{left:250px}.info-card.vision{left:630px}
.info-card .card-icon{position:absolute;left:125px;top:-35px;width:70px;height:70px;border-radius:50%;background:var(--blue-deep);display:flex;align-items:center;justify-content:center;box-shadow:0 0 0 4px var(--white)}
.info-card h3{font-family:"Roboto",sans-serif;font-size:26px;font-weight:500;color:var(--ink)}
.info-card p{font-size:11px;line-height:1.6;color:var(--grey);padding:12px 30px 0}

/* reviews */
.reviews{top:1460px;height:360px;background:linear-gradient(180deg,#3b4a58,#5d6b76 50%,#2f3c48)}
.reviews-backdrop{position:absolute;inset:0;background:radial-gradient(ellipse at 60% 70%,rgba(178,150,120,.35),rgba(0,0,0,0) 60%)}
.reviews .section-title{position:relative;margin-top:40px;color:var(--white);font-size:34px;font-weight:400}
.reviews-sub{position:relative;text-align:center;font-size:11px;color:#d6dde4;margin-top:6px}
.quote-box{position:absolute;left:150px;top:130px;width:820px;height:100px;background:rgba(255,255,255,.85);padding:18px 40px 0 60px;font-size:11px;line-height:1.6;color:#4a5560;font-style:italic}
.quote-box::before{content:"\201C";position:absolute;left:18px;top:2px;font-size:52px;color:var(--grey);font-style:normal;font-family:"Roboto",sans-serif}
.reviewer-photo{position:absolute;left:960px;top:120px;width:90px;height:90px;border-radius:50%;background:linear-gradient(#c9b39a,#8e7a66);border:4px solid var(--white)}
.reviewer-name{position:absolute;right:150px;top:245px;font-size:11px;color:#e4e9ee}
.reviews .slider-dots{left:152px;top:250px}
.reviews .slider-dots span{width:9px;height:9px;border-width:1px}

/* clients */
.clients{top:1820px;height:140px;background:linear-gradient(#e9eef2,#dfe6ec)}
.clients h2{position:absolute;left:150px;top:42px;font-family:"Roboto",sans-serif;font-weight:400;font-size:34px;line-height:1.05;color:var(--ink)}
.client-row{position:absolute;left:355px;top:48px;display:flex;gap:18px}
.client{width:130px;height:48px;display:flex;align-items:center;justify-content:center;gap:7px;font-family:"Open Sans",sans-serif;font-weight:700;font-size:20px;color:#33414d}
.client i{width:12px;height:12px;background:#33414d;display:block}

/* newsletter */
.newsletter{top:1960px;height:60px;background:var(--blue-mid);display:flex;align-items:center;padding-left:150px;gap:26px}
.newsletter h4{font-family:"Roboto",sans-serif;font-weight:400;font-size:17px;color:var(--white)}
.newsletter .field{width:480px;height:30px;background:var(--white);font-size:11px;color:#9aa4ae;padding:7px 12px}
.newsletter .subscribe{width:110px;height:30px;background:var(--green);color:var(--white);font-size:13px;text-align:center;line-height:30px;margin-left:-26px}

/* footer */
.site-footer{top:2020px;height:230px;background:var(--navy)}
.foot-col{position:absolute;top:26px}
.foot-col h5{font-family:"Roboto",sans-serif;font-weight:500;font-size:14px;color:var(--white);margin-bottom:12px;padding-bottom:6px;border-bottom:1px solid rgba(255,255,255,.2)}
.foot-col li{list-style:none;font-size:11px;color:#c5d6e8;line-height:2}
.foot-col.links{left:150px;width:150px}
.foot-col.contact{left:360px;width:230px}
.foot-col.map{left:640px;width:180px}
.foot-col.follow{left:900px;width:150px}
.contact li{display:flex;align-items:center;gap:8px}
.contact .dot{width:16px;height:16px;border-radius:50%;background:var(--blue-sky);flex:none}
.map-area{width:170px;height:110px;background:linear-gradient(135deg,#e8ebe6,#d3d9d2)}
.map-caption{font-size:10px;color:#c5d6e8;margin-top:6px}
.follow li{display:flex;align-items:center;gap:8px}
.follow .sq{width:18px;height:18px;background:var(--blue-mid);flex:none}
.copyright{position:absolute;left:0;width:1200px;top:2250px;height:30px;background:var(--navy-dark);text-align:center;font-size:10px;color:#a9bdd2;line-height:30px}
</style>
</head>
<body>

<header class="site-header">
  <div class="brand">
    <span class="brand-dot"></span>
    <span class="brand-name">Velirox</span>
  </div>
  <div class="header-phone">
    <svg width="16" height="16" viewBox="0 0 24 24"><path fill="#0555a3" d="M6.6 10.8a15 15 0 0 0 6.6 6.6l2.2-2.2c.3-.3.7-.4 1-.2 1.1.4 2.3.6 3.6.6.6 0 1 .4 1 1V20c0 .6-.4 1-1 1A17 17 0 0 1 3 4c0-.6.4-1 1-1h3.5c.6 0 1 .4 1 1 0 1.3.2 2.5.6 3.6.1.3 0 .7-.2 1z"/></svg>
    +45 71 82 64 93
  </div>
  <nav class="main-nav">
    <a class="active">HOME</a><a>WORK</a><a>EXPERTISE</a><a>APPROACH</a><a>CLIENTS</a><a>ABOUT</a><a>CONTACT</a>
  </nav>
</header>

<section class="hero">
  <div class="hero-visual" role="img" aria-label="Businessman holding a glowing world map network"></div>
  <h1 class="hero-title">We Provide Complete Services Throughout The Product Development Process</h1>
  <div class="slider-dots"><span class="on"></span><span></span><span></span><span></span></div>
</section>

<section class="services">
  <h2 class="section-title"><strong>OUR</strong> SERVICES</h2>
  <div class="title-rule"></div>
  <div class="arrow left">&#8249;</div>
  <div class="arrow right">&#8250;</div>
  <div class="service-list">
    <div class="service">
      <div class="service-icon"><svg width="34" height="34" viewBox="0 0 24 24" fill="none" stroke="#fff" stroke-width="1.8"><rect x="3" y="4" width="18" height="12" rx="1"/><path d="M9 20h6M12 16v4"/></svg></div>
      <h3>Design</h3>
      <p>We shape clear product ideas into smart and usable concepts for green markets.</p>
      <span class="more-btn">Read More</span>
    </div>
    <div class="service">
      <div class="service-icon"><svg width="34" height="34" viewBox="0 0 24 24" fill="none" stroke="#fff" stroke-width="1.8"><circle cx="12" cy="12" r="3.5"/><path d="M12 2v3M12 19v3M2 12h3M19 12h3M4.9 4.9l2.1 2.1M17 17l2.1 2.1M4.9 19.1 7 17M17 7l2.1-2.1"/></svg></div>
      <h3>Engineering</h3>
      <p>Solid technical work that turns each concept into a robust working solution.</p>
      <span class="more-btn">Read More</span>
    </div>
    <div class="service">
      <div class="service-icon"><svg width="34" height="34" viewBox="0 0 24 24" fill="none" stroke="#fff" stroke-width="1.8"><path d="M3 20V10l5 3V10l5 3V6h4v14z"/><path d="M3 20h18"/></svg></div>
      <h3>Manufacturing</h3>
      <p>Reliable production set up with trusted partners and steady quality control.</p>
      <span class="more-btn">Read More</span>
    </div>
    <div class="service">
      <div class="service-icon"><svg width="34" height="34" viewBox="0 0 24 24" fill="none" stroke="#fff" stroke-width="1.8"><path d="M3 7l9-4 9 4v10l-9 4-9-4z"/><path d="M3 7l9 4 9-4M12 11v10"/></svg></div>
      <h3>Sourcing</h3>
      <p>We find the right parts and suppliers at fair cost across the global market.</p>
      <span class="more-btn">Read More</span>
    </div>
    <div class="service">
      <div class="service-icon"><svg width="34" height="34" viewBox="0 0 24 24" fill="#fff"><circle cx="5" cy="12" r="2.2"/><circle cx="12" cy="12" r="2.2"/><circle cx="19" cy="12" r="2.2"/></svg></div>
      <h3>Other Processes</h3>
      <p>Support for testing, approval, logistics and every step toward market launch.</p>
      <span class="more-btn">Read More</span>
    </div>
  </div>
</section>

<section class="welcome">
  <h2 class="section-title">WELCOME TO <strong>VELIROX</strong> SUSTAINABLE SOLUTIONS</h2>
  <p class="welcome-intro">Velirox is a development company focused on green energy and sustainable products. We guide ideas from the first sketch through design, engineering, manufacturing and sourcing, working both as consultants for our clients and on our own solar products. Our team combines technical depth with a practical view of the market, so every project ends as a product that works.</p>
  <div class="info-card who">
    <div class="card-icon"><svg width="32" height="32" viewBox="0 0 24 24" fill="#fff"><circle cx="8" cy="8" r="3"/><circle cx="16" cy="8" r="3"/><path d="M2 19c0-3.5 2.7-6 6-6s6 2.5 6 6zM12 19c0-3.5 1.7-6 4-6 3.3 0 6 2.5 6 6z"/></svg></div>
    <h3>Who We Are</h3>
    <p>A young Danish team of engineers and designers who believe clean energy should be simple, durable and within reach for everyone.</p>
    <span class="more-btn">Read More</span>
  </div>
  <div class="info-card vision">
    <div class="card-icon"><svg width="32" height="32" viewBox="0 0 24 24" fill="none" stroke="#fff" stroke-width="2"><circle cx="12" cy="12" r="9"/><circle cx="12" cy="12" r="5"/><circle cx="12" cy="12" r="1.5" fill="#fff"/></svg></div>
    <h3>Our Vision</h3>
    <p>To bring sustainable products to market faster, making green technology the natural choice for companies and homes worldwide.</p>
    <span class="more-btn">Read More</span>
  </div>
</section>

<section class="reviews">
  <div class="reviews-backdrop" role="img" aria-label="Faded photo of hands joined in teamwork"></div>
  <h2 class="section-title">Our Customer Reviews</h2>
  <p class="reviews-sub">Read what our partners say about working with our team on their projects.</p>
  <p class="reviews-sub">Honest words from clients across many fields of green technology.</p>
  <div class="quote-box">Velirox took our rough idea and turned it into a finished product in record time. Their engineers were clear, quick and always open about costs. The sourcing work alone saved us months, and the final result exceeded what we hoped for. We will gladly work with them again on our next launch.</div>
  <div class="reviewer-photo" role="img" aria-label="Portrait of the reviewer"></div>
  <div class="reviewer-name">Henrik Dalby, CEO</div>
  <div class="slider-dots"><span class="on"></span><span></span><span></span></div>
</section>

<section class="clients">
  <h2>Our<br>Clients</h2>
  <div class="client-row">
    <div class="client"><i></i>Korvel</div>
    <div class="client">Nestria</div>
    <div class="client">Dalmont</div>
    <div class="client">Brevia</div>
    <div class="client">Tovara</div>
  </div>
</section>

<section class="newsletter">
  <h4>Subscribe to Our Newsletter</h4>
  <div class="field">Enter your email address</div>
  <div class="subscribe">Subscribe</div>
</section>

<footer class="site-footer">
  <div class="foot-col links">
    <h5>Quick Links</h5>
    <ul><li>› Home</li><li>› About</li><li>› Expertise</li><li>› Approach</li><li>› Clients</li><li>› Contact</li></ul>
  </div>
  <div class="foot-col contact">
    <h5>Contact Us</h5>
    <ul>
      <li><span class="dot"></span>Kildevej 58, 2 DK-8630 Halvby</li>
      <li><span class="dot"></span>+45 71 82 64 93</li>
      <li><span class="dot"></span>www.velirox.com</li>
      <li><span class="dot"></span>jonas.ulfkaer@velirox.dk</li>
    </ul>
  </div>
  <div class="foot-col map">
    <h5>Location Map</h5>
    <div class="map-area" role="img" aria-label="Street map showing the office location"></div>
    <div class="map-caption">View larger map</div>
  </div>
  <div class="foot-col follow">
    <h5>Follow Us</h5>
    <ul>
      <li><span class="sq"></span>Pagelink</li>
      <li><span class="sq"></span>Chirplet</li>
      <li><span class="sq"></span>Circlo</li>
      <li><span class="sq"></span>Workvine</li>
    </ul>
  </div>
</footer>
<div class="copyright">Copyright © 2015 Velirox ApS. All Rights Reserved.</div>

</body>
</html>
```